Summit Bodyform Gym Website

We need a website design for our gym.

Summit is the UAE's first calisthenics and parkour gym. The theme under which the gym revolves is that one does not require any machinery to workout as our bodies could be themselves the machinery. The gym is designed to be the more of a social hub rather than an "in-and-out" gym, where people come train, have fun, hang out and socialize for a few hours rather than just train for 60 minutes then leave. The gym is designed to be a big open space with lots of natural sunlight, natural wood and plants all over the place to create a natural and refreshing setting. We also use recycled material throughout the gym and recycle our waste as being green is part of our philosophy. We currently also have some of the world's top and most recognized calisthenics athletes working with us.

We would like our website to reflect all that as well as provide a simple, interactive and fun way for visitors to be able to get class and gym information, check out gym media and contact us for bookings.

Target Market(s)

Ages 15-35

Industry/Entity Type

Fitness

Coding

Coded - Design and coding required

Number of Pages Required

4 page

Font styles to use
Decorative

Colors
0792cd

Requirements
Must have
• Class descriptions
• Gym description
• Class schedules
• Trainer profiles
• Gym philosophy
• Contact Details
Nice to have
• A link to contact us directly for a free first trial class

```html
<!DOCTYPE html>
<html lang="en">
<head>
<meta charset="utf-8">
<title>Summit Bodyform Gym</title>
<link href="https://fonts.googleapis.com/css2?family=Roboto:wght@300;400;700&family=Roboto+Slab:wght@400&family=Montserrat:wght@400;600;800&family=Open+Sans:wght@400;600&display=swap" rel="stylesheet">
<style>
:root{
  --brand:#0792cd;
  --brand-nav:#1aa0c8;
  --ink:#222;
  --muted:#9a9a9a;
  --text:#333;
  --band:#f3f3f3;
  --line:#d4d4d4;
  --footer:#1c1b1b;
  --footer-deep:#0f0f0f;
  --white:#fff;
}
*{margin:0;padding:0;box-sizing:border-box}
html,body{width:1200px;height:3061px;overflow:hidden;background:var(--white)}
body{position:relative;font-family:'Open Sans',sans-serif;color:var(--text)}
.abs{position:absolute}

/* nav */
.site-nav{left:0;top:0;width:1200px;height:102px;background:var(--brand-nav);z-index:5}
.nav-link{top:0;height:102px;line-height:110px;font-family:'Roboto Slab',serif;font-size:20px;color:var(--white);text-align:center}
.nav-link.active{background:#262626}
.brand-badge{left:506px;top:0;width:188px;height:188px;border-radius:50%;background:var(--white);border:6px solid var(--brand-nav);display:flex;align-items:center;justify-content:center;z-index:10}
.brand-badge span{font-family:'Montserrat',sans-serif;font-weight:800;font-size:26px;color:#1c1c1c;text-align:center;line-height:1.1;white-space:nowrap}

/* hero */
.hero{left:0;top:102px;width:1200px;height:576px;background:linear-gradient(160deg,#3a3a3c 0%,#777 45%,#9c9a99 70%,#6a6a6a 100%)}
.hero-arrow{top:366px;width:48px;height:50px;background:#e9e9e9;color:#333;font-size:28px;line-height:46px;text-align:center;font-family:'Roboto',sans-serif;font-weight:700}

/* trial */
.trial{left:0;top:678px;width:1200px;height:155px;background:var(--band);text-align:center}
.trial h2{position:absolute;left:0;right:0;top:40px;font-family:'Montserrat',sans-serif;font-weight:800;font-size:34px;letter-spacing:1px;color:#151515}
.trial p{position:absolute;left:0;right:0;top:92px;font-family:'Montserrat',sans-serif;font-size:18px;color:#222}
.trial a{color:var(--brand);text-decoration:underline;margin-left:22px}

/* section heads */
.section-head{left:0;width:1200px;text-align:center}
.section-title{display:inline-flex;align-items:center;gap:18px;font-family:'Roboto',sans-serif;font-weight:300;font-size:44px;color:var(--brand);line-height:1;white-space:nowrap}
.section-title::before,.section-title::after{content:"";width:88px;height:1px;background:#9ab;flex:none}
.section-sub{margin-top:14px;font-family:'Roboto',sans-serif;font-weight:300;font-size:21px;color:var(--muted)}

/* class cards */
.class-card{top:1053px;width:249px;height:155px;border:1px solid var(--line);background:var(--white)}
.class-thumb{top:1002px;width:104px;height:104px;border-radius:50%;border:2px solid #555}
.class-card p{position:absolute;left:14px;right:14px;top:80px;text-align:center;font-size:15px;line-height:25px;color:#333}
.read-more{top:1190px;width:146px;height:42px;line-height:42px;text-align:center;background:var(--white);font-family:'Montserrat',sans-serif;font-weight:600;font-size:14px;color:var(--brand)}
.read-more.boxed{border:1px solid var(--line)}
.pager{width:47px;height:46px;border:1px solid #bbb;background:var(--white);text-align:center;line-height:42px;font-size:24px;font-weight:700;font-family:'Roboto',sans-serif;color:#222}

/* philosophy */
.philosophy{left:0;top:1365px;width:1200px;height:417px;background:#f4f4f4}
.philosophy-photo{left:0;top:0;width:470px;height:417px;background:linear-gradient(90deg,#b9c7d2 0%,#cfd8de 55%,#e8ecee 85%,#f4f4f4 100%)}
.philosophy-head{left:390px;width:560px;top:66px;text-align:center}
.philosophy-text{left:498px;top:198px;width:610px;font-family:'Montserrat',sans-serif;font-size:14.5px;line-height:25px;color:#222}
.dot{top:320px;width:12px;height:12px;border:1px solid #666;background:var(--white)}
.dot.on{background:var(--brand);border-color:var(--brand)}

/* team */
.trainer{top:1955px;width:249px;height:155px;background:linear-gradient(180deg,#5d5d5f,#3c3c3e)}
.trainer.focus{background:linear-gradient(180deg,#3aa9cf,#1a8cb8)}
.social-row{left:72px;top:64px;display:flex;gap:0}
.social-row i{display:block;width:26px;height:24px;border-left:1px solid rgba(255,255,255,.8);position:relative}
.social-row i:last-child{border-right:1px solid rgba(255,255,255,.8)}
.social-row i::after{content:"";position:absolute;left:8px;top:7px;width:10px;height:10px;background:var(--white)}
.rule{left:78px;top:2235px;width:1045px;height:1px;background:var(--line)}

/* description */
.about-text{left:170px;top:2402px;width:860px;text-align:center;font-size:15px;line-height:28px;color:#333}
.schedule-btn{left:486px;top:2535px;width:228px;height:55px;background:var(--brand);color:var(--white);font-family:'Roboto',sans-serif;font-size:21px;text-align:center;line-height:55px}

/* footer */
.footer{left:0;top:2643px;width:1200px;height:363px;background:var(--footer)}
.footer-brand{left:150px;top:72px;width:210px;text-align:center;font-family:'Montserrat',sans-serif;font-weight:800;font-size:34px;color:var(--white)}
.footer-brand small{display:block;font-size:12px;font-weight:400;margin-top:2px}
.footer-blurb{left:80px;top:172px;width:350px;text-align:center;font-size:14px;line-height:21px;color:var(--white)}
.footer-head{top:62px;font-family:'Roboto',sans-serif;font-weight:300;font-size:24px;color:var(--brand)}
.footer-links{left:514px;top:104px;list-style:none}
.footer-links li{font-size:14px;line-height:27.4px;color:var(--white);padding-left:26px;position:relative}
.footer-links li::before{content:"";position:absolute;left:2px;top:10px;width:8px;height:8px;border-radius:50%;background:var(--white)}
.contact-row{left:814px;width:320px;display:flex;gap:22px;font-size:14px;line-height:21px;color:var(--white)}
.contact-row svg{flex:none;margin-top:3px}
.footer-rule{left:78px;top:298px;width:1045px;height:1px;background:#333}
.footer-nav{left:80px;top:318px;font-size:14px;color:var(--white)}
.footer-nav span{margin-right:32px}
.footer-nav .sep{color:#ccc}
.footer-nav .current{color:var(--brand)}
.footer-social{top:325px;width:12px;height:12px;border-radius:50%;background:var(--white)}
.footer-social.alt{background:var(--brand)}
.copyright{left:0;top:3006px;width:1200px;height:55px;background:var(--footer-deep);text-align:center;line-height:55px;font-size:14px;color:var(--white)}
.copyright b{font-weight:400;color:var(--brand)}
</style>
</head>
<body>

<nav class="abs site-nav">
  <div class="abs nav-link active" style="left:112px;width:125px">HOME</div>
  <div class="abs nav-link" style="left:282px;width:130px">ABOUT</div>
  <div class="abs nav-link" style="left:750px;width:140px">SERVICES</div>
  <div class="abs nav-link" style="left:945px;width:155px">CONTACT US</div>
</nav>
<div class="abs brand-badge"><span>Summit<br>Bodyform</span></div>

<div class="abs hero" role="img" aria-label="Trainer coaching an athlete doing push-ups on kettlebells in a gym"></div>
<div class="abs hero-arrow" style="left:0">«</div>
<div class="abs hero-arrow" style="left:1152px">»</div>

<section class="abs trial">
  <h2>CONTACT US DIRECT FOR FREE FIRST TRIAL</h2>
  <p>Click here for first free Trial Now <a>www.summitbodyformgym.com</a></p>
</section>

<header class="abs section-head" style="top:884px">
  <div class="section-title">CLASS DESCRIPTION</div>
  <div class="section-sub">Classes &amp; Training programmes</div>
</header>

<div class="abs class-card" style="left:78px"><p>Lorem ipsum dolor sit amet, consectetur adipiscing elit, sed.</p></div>
<div class="abs class-card" style="left:343px"><p>Lorem ipsum dolor sit amet, consectetur adipiscing elit, sed.</p></div>
<div class="abs class-card" style="left:608px"><p>Lorem ipsum dolor sit amet, consectetur adipiscing elit, sed.</p></div>
<div class="abs class-card" style="left:874px"><p>Lorem ipsum dolor sit amet, consectetur adipiscing elit, sed.</p></div>
<div class="abs class-thumb" style="left:150px;background:radial-gradient(circle,#e4e0dc,#a9a5a2)" role="img" aria-label="Woman training with a fitness ball"></div>
<div class="abs class-thumb" style="left:415px;background:radial-gradient(circle,#6b7b8a,#2c3440)" role="img" aria-label="Gym equipment rack"></div>
<div class="abs class-thumb" style="left:681px;background:radial-gradient(circle,#e8e8e8,#9d9d9d)" role="img" aria-label="Man lifting dumbbells"></div>
<div class="abs class-thumb" style="left:946px;background:radial-gradient(circle,#f2c58a,#b46b3a)" role="img" aria-label="Runner at sunset"></div>
<div class="abs read-more boxed" style="left:130px">READ MORE</div>
<div class="abs read-more" style="left:395px">READ MORE</div>
<div class="abs read-more" style="left:661px">READ MORE</div>
<div class="abs read-more" style="left:926px">READ MORE</div>
<div class="abs pager" style="left:551px;top:1263px">«</div>
<div class="abs pager" style="left:604px;top:1263px">»</div>

<section class="abs philosophy">
  <div class="abs philosophy-photo" role="img" aria-label="Smiling man lifting dumbbells in a bright studio"></div>
  <header class="abs philosophy-head">
    <div class="section-title">OUR PHILOSOPHY</div>
    <div class="section-sub" style="margin-top:12px;font-size:19px">WHAT WE THINK</div>
  </header>
  <p class="abs philosophy-text">Lorem ipsum dolor sit amet, consectetur adipiscing elit, sed do eiusmod tempor incididunt ut labore et dolore magna aliqua. Ut enim ad minim veniam, quis nostrud exercitation ullamco laboris nisi ut aliquip ex ea commodo consequat.</p>
  <span class="abs dot" style="left:496px"></span>
  <span class="abs dot on" style="left:518px"></span>
  <span class="abs dot" style="left:540px"></span>
  <span class="abs dot" style="left:562px"></span>
  <span class="abs dot" style="left:584px"></span>
</section>

<header class="abs section-head" style="top:1835px">
  <div class="section-title">MEE OUR TEAM</div>
  <div class="section-sub">Trainers Profile</div>
</header>
<div class="abs trainer" style="left:78px" role="img" aria-label="Trainer profile photo, woman in hoodie"></div>
<div class="abs trainer focus" style="left:343px" role="img" aria-label="Trainer profile photo with social links overlay">
  <div class="abs social-row"><i></i><i></i><i></i><i></i></div>
</div>
<div class="abs trainer" style="left:608px" role="img" aria-label="Trainer profile photo, man in white shirt"></div>
<div class="abs trainer" style="left:874px" role="img" aria-label="Trainer profile photo, man in red shirt"></div>
<div class="abs pager" style="left:551px;top:2139px">«</div>
<div class="abs pager" style="left:604px;top:2139px">»</div>
<div class="abs rule"></div>

<header class="abs section-head" style="top:2286px">
  <div class="section-title">OUR DESCRIPTION</div>
  <div class="section-sub">Who We Are</div>
</header>
<p class="abs about-text">Summit is the UAE's first calisthenics and parkour gym. The theme under which the gym revolves is that one does not require any machinery to workout as our bodies could be themselves the machinery. The gym is designed to be the more of a social hub rather than an "in-and-out" gym, where people come train, have fun, hang out and socialize for a few hours rather than just train for 60 minutes then leave.</p>
<div class="abs schedule-btn">View Our Schedule</div>

<footer class="abs footer">
  <div class="abs footer-brand">Summit<small>Bodyform Gym</small></div>
  <p class="abs footer-blurb">Summit is Gym where people come train, have fun, hang out and socialize for a few hours rather than just train for 60 minutes then leave</p>

  <div class="abs footer-head" style="left:514px">Important Links</div>
  <ul class="abs footer-links">
    <li>Class descriptions</li>
    <li>Gym description</li>
    <li>Class schedules</li>
    <li>Trainer profiles</li>
    <li>Gym philosophy</li>
    <li>Contact Details</li>
  </ul>

  <div class="abs footer-head" style="left:814px">Keep In Touch With Us</div>
  <div class="abs contact-row" style="top:116px">
    <svg width="16" height="14" viewBox="0 0 16 14"><path d="M8 0L0 7h2v7h4V9h4v5h4V7h2z" fill="#fff"/></svg>
    <span>Lorem ipsum dolor sit amet, consectetur adipiscing elit, sed do eiusmod tempor.</span>
  </div>
  <div class="abs contact-row" style="top:168px">
    <svg width="16" height="16" viewBox="0 0 16 16"><path d="M3 1l3 3-2 2c1 2 3 4 5 5l2-2 3 3-2 3C6 15 1 10 0 4z" fill="#fff"/></svg>
    <span>+971 4 555 0192</span>
  </div>
  <div class="abs contact-row" style="top:206px">
    <svg width="16" height="12" viewBox="0 0 16 12"><rect width="16" height="12" fill="#fff"/><path d="M0 0l8 6 8-6" stroke="#1c1b1b" stroke-width="1.5" fill="none"/></svg>
    <span>hello@summitbodyform.example</span>
  </div>

  <div class="abs footer-rule"></div>
  <div class="abs footer-nav">
    <span class="current">Home</span><span class="sep">/</span><span>About</span><span class="sep">/</span><span>Services</span><span class="sep">/</span><span>Contact Us</span>
  </div>
  <span class="abs footer-social" style="left:994px"></span>
  <span class="abs footer-social alt" style="left:1026px"></span>
  <span class="abs footer-social" style="left:1056px"></span>
  <span class="abs footer-social" style="left:1088px"></span>
</footer>
<div class="abs copyright">© <b>summitbodyformgym</b> - 2015. All Rights Reserved.</div>

</body>
</html>
```